Label design for an exciting new Vodka brand

We need a label design for a dynamic new Vodka brand called 'Pale lantern drift Vodka'. It is a crisp and versatile liquid with a clean and smooth finish. It should appeal to 21-39 year olds, with a slight female skew. Colours, fonts and styles should be modern and relatively neutral - take inspiration from the brand pictures attached.

Target Market(s)

21-39 year olds, both male and female, but with a slight female skew

```html
<!DOCTYPE html>
<html lang="en">
<head>
<meta charset="UTF-8">
<title>Pale Lantern Drift Vodka – Label</title>
<link rel="stylesheet" href="https://fonts.googleapis.com/css2?family=Montserrat:wght@500;800&display=swap">
<style>
  :root {
    --page-bg: #ffffff;
    --gold-deep: #d5b06d;
    --gold-mid: #e6c98f;
    --gold-light: #fbefcf;
    --brand-purple: #7a3b96;
  }

  html, body {
    margin: 0;
    padding: 0;
    overflow: hidden;
  }

  body {
    width: 1200px;
    height: 1000px;
    background: var(--page-bg);
    display: flex;
    align-items: center;
    justify-content: center;
  }

  .label {
    position: relative;
    width: 645px;
    height: 860px;
    background: linear-gradient(
      150deg,
      var(--gold-deep) 0%,
      var(--gold-mid) 32%,
      var(--gold-light) 52%,
      var(--gold-mid) 76%,
      var(--gold-deep) 100%
    );
    overflow: hidden;
  }

  .label__wordmark {
    position: absolute;
    top: 300px;
    left: 0;
    right: 0;
    margin: 0;
    text-align: center;
    font-family: "Montserrat", sans-serif;
    font-weight: 800;
    font-size: 52px;
    line-height: 1.25;
    letter-spacing: 0.12em;
    text-transform: uppercase;
    color: var(--brand-purple);
  }

  .label__wordmark-line {
    display: block;
  }

  .label__category {
    position: absolute;
    left: 50%;
    top: 610px;
    transform: translate(-50%, -50%) rotate(-90deg);
    margin: 0;
    font-family: "Montserrat", sans-serif;
    font-weight: 500;
    font-size: 30px;
    letter-spacing: 0.18em;
    text-transform: uppercase;
    color: var(--brand-purple);
    white-space: nowrap;
  }
</style>
</head>
<body>
  <main class="label" aria-label="Pale Lantern Drift Vodka bottle label">
    <h1 class="label__wordmark">
      <span class="label__wordmark-line">Pale Lantern</span>
      <span class="label__wordmark-line">Drift</span>
    </h1>
    <p class="label__category">Vodka</p>
  </main>
</body>
</html>
```